Help me make landing pages for my web application that are mobile friendly

I need to make 2 mobile friendly landing pages for an application. The 2 pages will be related. First I need a home page and then I need a working page. I do not want to change the color scheme or logos. Just layout and design.

```html
<!DOCTYPE html>
<html lang="en">
<head>
<meta charset="UTF-8">
<title>My Assignments</title>
<link href="https://fonts.googleapis.com/css2?family=Inter:wght@400;500;600&display=swap" rel="stylesheet">
<style>
  :root {
    --page-bg: #ececec;
    --screen-bg: #f4f4f5;
    --card-bg: #ffffff;
    --ink: #111111;
    --muted: #444444;
    --accent: #2fb3d4;
    --purple: #7455ad;
    --active: #4bb543;
    --canceled: #e53935;
    --complete: #f5a23a;
    --soft-grey: #f1f1f2;
    --lavender: #dcd6ec;
    --teal-glow: #b9e2ea;
    --alert: #f04438;
  }
  * { box-sizing: border-box; margin: 0; padding: 0; }
  html, body { width: 849px; height: 1200px; overflow: hidden; }
  body { background: var(--page-bg); font-family: "Inter", Helvetica, Arial, sans-serif; color: var(--ink); position: relative; }

  .app-screen {
    position: absolute; left: 162px; top: 25px; width: 524px; height: 1150px;
    border-radius: 56px; overflow: hidden;
    background:
      radial-gradient(ellipse 140px 220px at 0px 700px, var(--teal-glow), transparent 70%),
      radial-gradient(ellipse 160px 260px at 524px 180px, var(--lavender), transparent 70%),
      var(--screen-bg);
  }
  .status-bar { position: absolute; top: 26px; left: 59px; right: 44px; height: 30px; display: flex; align-items: center; justify-content: space-between; }
  .status-time { font-size: 25px; font-weight: 600; letter-spacing: -0.5px; }
  .status-icons { display: flex; gap: 8px; align-items: center; }

  .profile { position: absolute; left: 58px; top: 78px; display: flex; align-items: center; gap: 12px; }
  .profile-photo { width: 48px; height: 48px; border-radius: 50%; background: radial-gradient(circle at 50% 40%, #a0537a, #3b2a6e 70%); }
  .profile-name { font-size: 22px; font-weight: 500; line-height: 1.1; }
  .profile-email { font-size: 13.5px; color: #222; }
  .bell { position: absolute; left: 446px; top: 90px; }

  .tab-switch { position: absolute; left: 54px; top: 141px; width: 419px; height: 57px; background: #fff; border-radius: 29px; }
  .tab { position: absolute; top: 4px; height: 50px; border-radius: 25px; display: flex; align-items: center; justify-content: center; font-size: 16.5px; }
  .tab-active { left: 4px; width: 218px; background: var(--accent); color: #fff; }
  .tab-idle { left: 222px; width: 197px; color: var(--ink); }

  .section-title { position: absolute; left: 54px; top: 224px; font-size: 21px; font-weight: 600; }

  .scroll-thumb { position: absolute; left: 488px; top: 445px; width: 5px; height: 68px; border-radius: 3px; background: #d6d3e4; }

  .assignment-card { position: absolute; left: 54px; width: 419px; height: 214px; background: var(--card-bg); border-radius: 28px; }
  .card-label { position: absolute; left: 37px; top: 31px; font-size: 18px; font-weight: 600; }
  .edit-button { position: absolute; left: 344px; top: 23px; width: 50px; height: 50px; border-radius: 50%; background: var(--soft-grey); display: flex; align-items: center; justify-content: center; }
  .person-photo { position: absolute; left: 35px; top: 67px; width: 50px; height: 50px; border-radius: 50%; }
  .photo-blue { background: radial-gradient(circle at 50% 45%, #9aa4ad, #4d5c6b 75%); }
  .photo-pink { background: radial-gradient(circle at 50% 45%, #d6a06d, #eeb8c4 70%); }
  .online-dot { position: absolute; left: 76px; top: 66px; width: 9px; height: 9px; border-radius: 50%; background: var(--active); border: 1.5px solid #fff; }
  .initials { position: absolute; left: 35px; top: 67px; width: 50px; height: 50px; border-radius: 50%; background: var(--soft-grey); color: var(--purple); font-size: 18px; font-weight: 500; display: flex; align-items: center; justify-content: center; }
  .details { position: absolute; left: 95px; top: 71px; font-size: 15px; line-height: 22.3px; color: var(--muted); white-space: nowrap; }
  .person-name { color: var(--accent); font-size: 16px; font-weight: 500; }
  .details b { color: var(--ink); font-weight: 500; }
  .status-active { color: var(--active); }
  .status-canceled { color: var(--canceled); }
  .status-complete { color: var(--complete); }
  .card-faded { opacity: 0.55; }

  .bottom-fade { position: absolute; left: 0; right: 0; top: 1000px; height: 150px; background: linear-gradient(to bottom, rgba(244,244,245,0), var(--screen-bg) 30%); }
  .nav-bar { position: absolute; left: 54px; top: 1019px; width: 419px; height: 57px; border-radius: 29px; background: linear-gradient(90deg, #e6f4f7, #f3f3f5 50%, #e7e2f1); }
  .nav-icon { position: absolute; top: 15px; }
  .nav-fab { position: absolute; left: 235px; top: 998px; width: 52px; height: 52px; border-radius: 50%; background: var(--purple); display: flex; align-items: center; justify-content: center; }
  .nav-label { position: absolute; left: 221px; top: 1058px; width: 80px; text-align: center; font-size: 9px; color: #555; }
</style>
</head>
<body>
<main class="app-screen">
  <div class="status-bar">
    <span class="status-time">9:41</span>
    <span class="status-icons">
      <svg width="28" height="18" viewBox="0 0 28 18"><rect x="0" y="11" width="5" height="7" rx="1"/><rect x="7" y="8" width="5" height="10" rx="1"/><rect x="14" y="4" width="5" height="14" rx="1"/><rect x="21" y="0" width="5" height="18" rx="1"/></svg>
      <svg width="24" height="18" viewBox="0 0 24 18" fill="none" stroke="#111" stroke-width="3" stroke-linecap="round"><path d="M2 6a14 14 0 0 1 20 0"/><path d="M6 10a8 8 0 0 1 12 0"/><circle cx="12" cy="15" r="1.5" fill="#111"/></svg>
      <svg width="34" height="16" viewBox="0 0 34 16"><rect x="1" y="1" width="29" height="14" rx="4" fill="none" stroke="#bbb"/><rect x="3" y="3" width="25" height="10" rx="2.5" fill="#111"/><rect x="31.5" y="5" width="2" height="6" rx="1" fill="#bbb"/></svg>
    </span>
  </div>

  <header class="profile">
    <div class="profile-photo" role="img" aria-label="Profile photo of the signed-in substitute"></div>
    <div>
      <div class="profile-name">Marisol</div>
      <div class="profile-email">m.sub.4@sample.org</div>
    </div>
  </header>
  <svg class="bell" width="28" height="28" viewBox="0 0 28 28"><path d="M12 3h2a1 1 0 0 1 1 1v1.2A7 7 0 0 1 20.5 12v5l2.5 3v1.5H3V20l2.5-3v-5A7 7 0 0 1 11 5.2V4a1 1 0 0 1 1-1z" fill="#111"/><path d="M10.5 23h5a2.5 2.5 0 0 1-5 0z" fill="#111"/><circle cx="22" cy="5" r="3.2" fill="var(--alert)"/></svg>

  <nav class="tab-switch">
    <div class="tab tab-active">My Assignments</div>
    <div class="tab tab-idle">Available Openings</div>
  </nav>

  <h1 class="section-title">My Assignments</h1>
  <div class="scroll-thumb"></div>

  <article class="assignment-card" style="top:268px">
    <div class="card-label">Subbing For:</div>
    <div class="edit-button"><svg width="20" height="20" viewBox="0 0 20 20" fill="none" stroke="#222" stroke-width="1.3" stroke-linejoin="round"><path d="M4 14l1-4 8-8 3 3-8 8z"/><path d="M11 4l3 3"/><path d="M2 18.5h16"/></svg></div>
    <div class="person-photo photo-blue" role="img" aria-label="Photo of the administrator"></div>
    <div class="online-dot"></div>
    <div class="details">
      <div class="person-name">Owen Hartley</div>
      <div>Administrator</div>
      <div><b>Location:</b> RVHS</div>
      <div><b>Status:</b><span class="status-active">Active</span></div>
      <div><b>Time Slots:</b>07/26 - 08/07 (14h 15m)</div>
    </div>
  </article>

  <article class="assignment-card" style="top:493px">
    <div class="card-label">Subbing For:</div>
    <div class="edit-button"><svg width="20" height="20" viewBox="0 0 20 20" fill="none" stroke="#222" stroke-width="1.3" stroke-linejoin="round"><path d="M4 14l1-4 8-8 3 3-8 8z"/><path d="M11 4l3 3"/><path d="M2 18.5h16"/></svg></div>
    <div class="person-photo photo-pink" role="img" aria-label="Photo of the teacher"></div>
    <div class="online-dot"></div>
    <div class="details">
      <div class="person-name">Priya Caldwell</div>
      <div>Teacher</div>
      <div><b>Location:</b> RVHS</div>
      <div><b>Status:</b><span class="status-canceled">Canceled</span></div>
      <div><b>Time Slots:</b>07/31 - 07/31 (9h 0m)</div>
    </div>
  </article>

  <article class="assignment-card" style="top:719px">
    <div class="card-label">Subbing For:</div>
    <div class="edit-button"><svg width="20" height="20" viewBox="0 0 20 20" fill="none" stroke="#222" stroke-width="1.3" stroke-linejoin="round"><path d="M4 14l1-4 8-8 3 3-8 8z"/><path d="M11 4l3 3"/><path d="M2 18.5h16"/></svg></div>
    <div class="initials">NR</div>
    <div class="details">
      <div class="person-name">Nolan Reyes</div>
      <div>Teacher</div>
      <div><b>Location:</b> RVHS</div>
      <div><b>Status:</b><span class="status-complete">Complete</span></div>
      <div><b>Time Slots:</b>07/31 - 07/31 (9h 0m)</div>
    </div>
  </article>

  <article class="assignment-card card-faded" style="top:944px">
    <div class="card-label">Subbing For:</div>
    <div class="edit-button"><svg width="20" height="20" viewBox="0 0 20 20" fill="none" stroke="#222" stroke-width="1.3" stroke-linejoin="round"><path d="M4 14l1-4 8-8 3 3-8 8z"/><path d="M11 4l3 3"/><path d="M2 18.5h16"/></svg></div>
  </article>

  <div class="bottom-fade"></div>

  <nav class="nav-bar">
    <svg class="nav-icon" style="left:35px" width="22" height="22" viewBox="0 0 22 22"><path d="M11 2l10 9h-3v9h-5v-6H9v6H4v-9H1z" fill="#111"/></svg>
    <svg class="nav-icon" style="left:108px" width="20" height="24" viewBox="0 0 20 24"><path d="M2 1h10l6 6v16H2z" fill="#111"/><path d="M6 12h8M6 15.5h8M6 19h8" stroke="#fff" stroke-width="1.6"/></svg>
    <svg class="nav-icon" style="left:291px" width="24" height="24" viewBox="0 0 24 24"><circle cx="12" cy="12" r="11" fill="#111"/><circle cx="12" cy="9.5" r="4" fill="#fff"/><path d="M5 19a8 6 0 0 1 14 0a10 10 0 0 1-14 0z" fill="#fff"/></svg>
    <svg class="nav-icon" style="left:364px" width="26" height="24" viewBox="0 0 26 24" fill="none" stroke="#111" stroke-width="2.8" stroke-linecap="round" stroke-linejoin="round"><path d="M15 5.5A9 9 0 1 0 15 18.5"/><path d="M11 12h13M20 8l4 4-4 4"/></svg>
  </nav>
  <div class="nav-fab"><svg width="18" height="22" viewBox="0 0 20 24"><path d="M2 1h10l6 6v16H2z" fill="#fff"/><path d="M6 12h8M6 15.5h8M6 19h8" stroke="var(--purple)" stroke-width="1.6"/></svg></div>
  <div class="nav-label">Assignments</div>
</main>
</body>
</html>
```